Fabric Store Business card

Need a business card portraying store logo and up and coming business of quilt fabrics, apparel fabrics, notions and buttons. Our business name is Gilded Thimble and Beyond. Am attaching logo. The design should communicate a growing business and warm atmosphere. Would like address and store hours and contact info displayed on card. Mon - Fri 9:30 to 5:00, Saturday 9:30 to 1:00. Address 784 W Orchard Ave, Newton, KS 67230 email: gildedthimblebeyond@mailvexa.com. Phone and fax 316-527-3486. After hours contact # 620-431-9052 Also like vintage sewing machines and dress forms if it works to incorporate fine, if not thats ok too.
Store

```html
<!DOCTYPE html>
<html lang="en">
<head>
<meta charset="utf-8">
<title>Gilded Thimble and Beyond – Business Card</title>
<link rel="stylesheet" href="https://fonts.googleapis.com/css2?family=Great+Vibes&family=Questrial&display=swap">
<style>
  :root {
    --bg: #2a2a2c;
    --card: #ffffff;
    --card-shade: #ececec;
    --red: #c0202f;
    --ink: #222222;
    --ink-soft: #444444;
    --stitch: #333333;
    --blush: #f2d4d7;
    --muted-rose: #d9a9ae;
  }
  * { margin: 0; padding: 0; box-sizing: border-box; }
  html, body { width: 1200px; height: 900px; overflow: hidden; }
  body {
    background: var(--bg);
    font-family: "Questrial", "Century Gothic", sans-serif;
    color: var(--ink);
    position: relative;
  }
  .card {
    position: absolute;
    top: 295px;
    width: 540px;
    height: 310px;
    background: linear-gradient(160deg, var(--card) 55%, var(--card-shade));
    overflow: hidden;
    border-radius: 2px;
  }
  .card--hours { left: 40px; }
  .card--contact { left: 620px; }

  .stitch-frame {
    position: absolute;
    inset: 16px;
    border: 1.6px dashed var(--stitch);
    border-radius: 26px;
  }
  .corner-disc {
    position: absolute;
    top: -58px;
    right: -30px;
    width: 140px;
    height: 140px;
    border-radius: 50%;
    background: var(--blush);
    opacity: .85;
  }
  .brand-name {
    position: absolute;
    font-family: "Questrial", "Century Gothic", sans-serif;
    font-size: 28px;
    font-weight: 400;
    color: var(--red);
    white-space: nowrap;
    line-height: 1;
  }
  .scissors-art {
    position: absolute;
    background: linear-gradient(135deg, var(--muted-rose), var(--blush));
    border-radius: 14px;
    opacity: .75;
  }

  /* hours side */
  .card--hours .brand-name { left: 96px; top: 66px; }
  .card--hours .scissors-art { left: 40px; top: 178px; width: 58px; height: 92px; }
  .hours__title {
    position: absolute;
    left: 150px;
    top: 104px;
    font-family: "Great Vibes", cursive;
    font-weight: 400;
    font-size: 40px;
    line-height: 1.1;
    color: var(--ink);
  }
  .hours__slot {
    position: absolute;
    display: flex;
    flex-direction: column;
    align-items: flex-start;
    gap: 4px;
  }
  .hours__slot--weekday { left: 150px; top: 184px; }
  .hours__slot--saturday { left: 318px; top: 162px; }
  .hours__pill {
    background: var(--red);
    color: #fff;
    font-size: 15px;
    padding: 2px 12px;
    border-radius: 12px;
  }
  .hours__time {
    font-size: 17px;
    color: var(--ink);
    padding-left: 14px;
  }
  .hours__after {
    position: absolute;
    left: 150px;
    top: 248px;
    font-size: 14px;
    color: var(--red);
  }

  /* contact side */
  .card--contact .brand-name { left: 110px; top: 70px; }
  .person {
    position: absolute;
    right: 58px;
    top: 140px;
    text-align: right;
  }
  .person__name { font-size: 22px; color: var(--red); letter-spacing: .5px; }
  .person__role { font-size: 12px; color: var(--ink-soft); }
  .card--contact .scissors-art { right: 62px; top: 196px; width: 130px; height: 42px; }
  .contact-tab {
    position: absolute;
    left: 0;
    top: 160px;
    width: 40px;
    height: 122px;
    background: var(--red);
    border-radius: 0 10px 10px 0;
    display: flex;
    flex-direction: column;
    align-items: center;
    justify-content: space-around;
    padding: 6px 0;
  }
  .contact-tab svg { width: 18px; height: 18px; fill: #fff; }
  .contact-list {
    position: absolute;
    left: 56px;
    top: 164px;
    list-style: none;
    display: flex;
    flex-direction: column;
    gap: 13px;
    font-size: 14px;
    color: var(--ink);
  }
</style>
</head>
<body>

<section class="card card--hours" aria-label="Store hours side">
  <div class="corner-disc"></div>
  <div class="stitch-frame"></div>
  <p class="brand-name">Gilded Thimble and Beyond</p>
  <div class="scissors-art" role="img" aria-label="Faint illustration of sewing scissors"></div>
  <h2 class="hours__title">Store hours</h2>
  <div class="hours__slot hours__slot--weekday">
    <span class="hours__pill">Mon - Fri</span>
    <span class="hours__time">9:30 to 5:00</span>
  </div>
  <div class="hours__slot hours__slot--saturday">
    <span class="hours__pill">Saturday</span>
    <span class="hours__time">9:30 to 1:00</span>
  </div>
  <p class="hours__after">After hours contact # 620-431-9052</p>
</section>

<section class="card card--contact" aria-label="Contact side">
  <div class="corner-disc"></div>
  <div class="stitch-frame"></div>
  <p class="brand-name">Gilded Thimble and Beyond</p>
  <div class="person">
    <p class="person__name">YOUR NAME</p>
    <p class="person__role">Designation</p>
  </div>
  <div class="scissors-art" role="img" aria-label="Faint illustration of sewing scissors"></div>

  <div class="contact-tab">
    <svg viewBox="0 0 24 24" aria-label="Phone"><path d="M6.6 10.8a15 15 0 0 0 6.6 6.6l2.2-2.2c.3-.3.7-.4 1-.2 1.1.4 2.3.6 3.6.6.6 0 1 .4 1 1V20c0 .6-.4 1-1 1A17 17 0 0 1 3 4c0-.6.4-1 1-1h3.5c.6 0 1 .4 1 1 0 1.3.2 2.5.6 3.6.1.3 0 .7-.2 1z"/></svg>
    <svg viewBox="0 0 24 24" aria-label="Fax"><path d="M7 3h10v5H7zM4 9h16a2 2 0 0 1 2 2v6h-4v4H6v-4H2v-6a2 2 0 0 1 2-2zm4 7v3h8v-3z"/></svg>
    <svg viewBox="0 0 24 24" aria-label="Email"><path d="M2 5h20v14H2zm2 2v.5l8 5.5 8-5.5V7l-8 5.3z"/></svg>
    <svg viewBox="0 0 24 24" aria-label="Address"><path d="M12 2a7 7 0 0 0-7 7c0 5 7 13 7 13s7-8 7-13a7 7 0 0 0-7-7zm0 9.5A2.5 2.5 0 1 1 12 6.5a2.5 2.5 0 0 1 0 5z"/></svg>
  </div>
  <ul class="contact-list">
    <li>316-527-3486</li>
    <li>316-527-3486</li>
    <li>gildedthimblebeyond@mailvexa.com</li>
    <li>784 W Orchard Ave, Newton, KS 67230</li>
  </ul>
</section>

</body>
</html>
```